Modernize and improve usability of our webpage www.lernwandel.ch (4 languages, mostly static content)

Need to modernize and freshen up the webpages of our association: www.lernwandel.ch We offer apprenticeship exchanges within Switzerland and abroad. Young people can inform and enroll online. We do the matchmaking with work locations and organize logistics, stay overs etc.
The webpage needs to be in 4 languages (German, French, Italian and English). The main pages will be:
- Landing page: what we do, targeted to our apprentices / young people who enroll for the stages.
- Sup-Page: Registration form for interested apprentices to sign up for the program
- Sub-Page "Company", the firms who would like to send their apprentices on a internship and info on how to join the program
- Sub-Page "Host Family", private people who would be interested in hosting the apprentices (for free) during the stages. Find out about the reqiurements for the host families
- Sub-Page "About Us", who we are, executive team, board of director, our sponsor "Falkner Circle Switzerland"
- Footer: contact (E-Mail, Telephone, WhatsApp), Bank details (IBAN Number), Partnerlogo of Falkner-Circle (see uploaded jpg), Social-Media Links (Facebook, LinkedIn)

Target Market(s)

Young people looking for a "apprenticeship" stage within Switzerland or going from Switzerland abroad

Industry/Entity Type

Apprenticeships: cooks, builders, craftsman, office support, etc.

Number of Pages Required

5+ page

Font styles to use
Other font styles liked:
• Lato (sans serif)

Requirements
Must have
• use colors shown on uploaded PDF-Slides: Make the BLUE the MAIN color, the ORANGE as a secondary color
Nice to have
• Forms using e.g. google forms or survey-monkey forms (external links, no code). Matching & appealing visuals showing young apprentices (can use stock photos)

```html
<!DOCTYPE html>
<html lang="en">
<head>
<meta charset="utf-8">
<title>Lernwandel – Apprentice Exchange</title>
<link href="https://fonts.googleapis.com/css2?family=Roboto:wght@400;500;700;900&display=swap" rel="stylesheet">
<style>
:root{
  --blue:#1f4e8c;
  --blue-dark:#18315f;
  --orange:#cc4d00;
  --orange-light:#e06a1c;
  --ink:#222;
  --muted:#666;
  --panel:#f2f2f2;
  --white:#fff;
}
*{box-sizing:border-box;margin:0;padding:0}
html,body{width:1200px;height:3711px;overflow:hidden}
body{font-family:'Roboto',sans-serif;color:var(--ink);background:var(--white);position:relative}
section,header,footer{position:relative;width:1200px;overflow:hidden}
.abs{position:absolute}
.btn{position:absolute;display:flex;align-items:center;justify-content:center;border-radius:22px;color:var(--white);font-weight:700;font-size:14px;text-transform:uppercase;text-decoration:none}
.btn--orange{background:var(--orange)}
.btn--blue{background:var(--blue)}

/* hero */
.hero{height:687px;background:linear-gradient(180deg,#1c3566 0%,#24497f 45%,#1f3d6b 75%,#173055 100%)}
.hero__scene{position:absolute;inset:0;background:linear-gradient(100deg,rgba(40,70,110,.2),rgba(60,100,90,.25) 60%,rgba(20,40,70,.3))}
.logo{position:absolute;color:var(--white);font-weight:500;letter-spacing:-1px}
.hero .logo{left:112px;top:12px;font-size:46px}
.nav{position:absolute;top:39px;left:398px;display:flex;gap:0}
.nav a{position:absolute;white-space:nowrap;color:var(--white);font-size:14px;font-weight:500;text-decoration:none}
.nav a.is-active{color:var(--orange-light)}
.lang{position:absolute;left:848px;top:32px}
.hero .btn--register{left:925px;top:27px;width:164px;height:40px;font-size:14px}
.hero__title{position:absolute;left:112px;top:262px;font-size:54px;font-weight:700;color:var(--white)}
.hero__text{position:absolute;left:112px;top:330px;width:450px;font-size:14.5px;line-height:26px;color:var(--white)}
.hero .btn--start{left:112px;top:424px;width:163px;height:39px}
.dots{position:absolute;left:112px;top:582px;display:flex;gap:4px}
.dots span{width:12px;height:12px;border-radius:50%;background:rgba(255,255,255,.55)}
.dots span:first-child{background:var(--white)}
.hero__portrait{position:absolute;left:612px;top:144px;width:518px;height:543px;border-radius:259px 259px 0 0;border:8px solid #1d4f9c;border-bottom:none;background:radial-gradient(circle at 50% 40%,#d9c3b0 0 18%,#e9e9ea 30%,#7aa25a 55%,#3f6b3a 100%)}

/* what we do */
.services{height:832px;background:var(--orange)}
.section-title{position:absolute;left:0;width:1200px;text-align:center;font-weight:700;font-size:50px}
.services .section-title{top:783px;top:96px;color:var(--white)}
.card{position:absolute;width:468px;height:218px;background:var(--white)}
.card__shot{position:absolute;left:0;top:-33px}
.card__title{position:absolute;left:203px;top:45px;font-size:19px;font-weight:500;color:var(--ink)}
.card__text{position:absolute;left:184px;top:82px;width:265px;font-size:13.5px;line-height:26px;color:var(--muted)}
.card__more{position:absolute;left:415px;top:169px;width:35px;height:35px;background:var(--blue);display:flex;align-items:center;justify-content:center}

/* about */
.about{height:1184px}
.about .section-title{top:88px;color:var(--ink)}
.about__lead{position:absolute;left:197px;top:162px;width:806px;font-size:13.5px;line-height:26px;color:var(--muted);text-align:justify;text-align-last:center}
.feature-photo{position:absolute}
.feature-box{position:absolute;border:1px solid #cfcfcf;background:var(--white);padding:26px 36px}
.feature-box h3{font-size:20px;font-weight:400;color:var(--blue);margin-bottom:16px}
.feature-box p{font-size:12.5px;line-height:21.5px;color:var(--muted);text-align:justify}
.feature-box--right h3,.feature-box--right p{text-align:right}
.feature-box--right p{text-align:justify;text-align-last:right}

/* stories */
.stories{height:357px}
.story__name{position:absolute;top:80px;font-size:52px;line-height:60px;font-weight:900;color:var(--white);text-transform:uppercase}

/* contact */
.contact{height:440px}
.contact .logo{left:0;width:1200px;text-align:center;top:70px;font-size:76px;color:var(--ink)}
.info{position:absolute;top:221px;width:305px;height:127px;background:var(--panel);text-align:center}
.info__icon{position:absolute;left:122px;top:-35px;width:60px;height:60px;border-radius:50%;background:var(--orange);display:flex;align-items:center;justify-content:center}
.info__label{position:absolute;left:0;width:100%;top:58px;font-size:15px;font-weight:700}
.info__value{position:absolute;left:0;width:100%;top:92px;font-size:16px;color:#444}

/* footer */
.site-footer{height:211px;background:var(--blue);color:var(--white)}
.partner{position:absolute;left:110px;top:43px;display:flex;align-items:center;gap:10px;font-size:30px;font-weight:500}
.partner span.mark{width:42px;height:42px;border-radius:50%;border:3px solid var(--white)}
.legal{position:absolute;right:111px;top:56px;font-size:13px}
.iban h4{position:absolute;left:113px;top:126px;font-size:20px;font-weight:700}
.iban p{position:absolute;left:113px;top:166px;font-size:13px}
.follow{position:absolute;left:868px;top:128px;font-size:20px;font-weight:700}
.social{position:absolute;top:124px;width:40px;height:40px;border-radius:50%;background:#2d63a8}
</style>
</head>
<body>

<header class="hero">
  <div class="hero__scene" role="img" aria-label="Evening view of a Swiss old town by the river, tinted blue"></div>
  <div class="logo">lernwandel</div>
  <nav class="nav">
    <a class="is-active" href="#" style="left:0">Home</a>
    <a href="#" style="left:64px">Company</a>
    <a href="#" style="left:151px">Host Family</a>
    <a href="#" style="left:254px">About Us</a>
    <a href="#" style="left:339px">Contact</a>
  </nav>
  <svg class="lang" width="32" height="32" viewBox="0 0 32 32" aria-label="English">
    <circle cx="16" cy="16" r="15" fill="#fff"/>
    <rect x="13" y="1" width="6" height="30" fill="#d6253c"/>
    <rect x="1" y="13" width="30" height="6" fill="#d6253c"/>
  </svg>
  <a class="btn btn--orange btn--register" href="#">Register Now</a>
  <h1 class="hero__title">Lernwandel</h1>
  <p class="hero__text">Lernwandel has been organizing the exchange of apprentices between different cultural and language regions within Switzerland as well as with other countries for more than 19 years.</p>
  <a class="btn btn--orange btn--start" href="#">Get Started</a>
  <div class="dots"><span></span><span></span><span></span></div>
  <div class="hero__portrait" role="img" aria-label="Portrait of a smiling apprentice in a white polo shirt in front of a Swiss town"></div>
</header>

<section class="services">
  <h2 class="section-title">What We Do</h2>

  <div class="card" style="left:112px;top:221px">
    <svg class="card__shot" width="215" height="233" viewBox="0 0 215 233" role="img" aria-label="Apprentice florist holding a bouquet">
      <defs><linearGradient id="g1" x1="0" y1="0" x2="1" y2="1"><stop offset="0" stop-color="#5a5a52"/><stop offset="1" stop-color="#a7b07a"/></linearGradient></defs>
      <polygon points="0,0 215,0 105,233" fill="var(--orange)"/>
      <polygon points="12,0 203,0 105,208" fill="url(#g1)"/>
    </svg>
    <h3 class="card__title">Lorem ipsum dolor</h3>
    <p class="card__text">Lorem ipsum dolor sit amet, consectetur adipiscing elit, sed do eiusmod tempor incididunt ut labore et dolore</p>
    <a class="card__more" href="#"><svg width="12" height="12" viewBox="0 0 12 12"><path d="M2 2l4 4-4 4M6 2l4 4-4 4" stroke="#fff" stroke-width="1.6" fill="none"/></svg></a>
  </div>

  <div class="card" style="left:620px;top:221px">
    <svg class="card__shot" width="215" height="233" viewBox="0 0 215 233" role="img" aria-label="Apprentice in white shirt in a workshop">
      <defs><linearGradient id="g2" x1="0" y1="0" x2="1" y2="1"><stop offset="0" stop-color="#2b2624"/><stop offset="1" stop-color="#d8cfc6"/></linearGradient></defs>
      <polygon points="0,0 215,0 105,233" fill="var(--orange)"/>
      <polygon points="12,0 203,0 105,208" fill="url(#g2)"/>
    </svg>
    <h3 class="card__title">Lorem ipsum dolor</h3>
    <p class="card__text">Lorem ipsum dolor sit amet, consectetur adipiscing elit, sed do eiusmod tempor incididunt ut labore et dolore</p>
    <a class="card__more" href="#"><svg width="12" height="12" viewBox="0 0 12 12"><path d="M2 2l4 4-4 4M6 2l4 4-4 4" stroke="#fff" stroke-width="1.6" fill="none"/></svg></a>
  </div>

  <div class="card" style="left:112px;top:497px">
    <svg class="card__shot" width="215" height="233" viewBox="0 0 215 233" role="img" aria-label="Apprentice in a black cap in a cafe">
      <defs><linearGradient id="g3" x1="0" y1="0" x2="1" y2="1"><stop offset="0" stop-color="#3b2a24"/><stop offset="1" stop-color="#1d1d1f"/></linearGradient></defs>
      <polygon points="0,0 215,0 105,233" fill="var(--orange)"/>
      <polygon points="12,0 203,0 105,208" fill="url(#g3)"/>
    </svg>
    <h3 class="card__title">Lorem ipsum dolor</h3>
    <p class="card__text">Lorem ipsum dolor sit amet, consectetur adipiscing elit, sed do eiusmod tempor incididunt ut labore et dolore</p>
    <a class="card__more" href="#"><svg width="12" height="12" viewBox="0 0 12 12"><path d="M2 2l4 4-4 4M6 2l4 4-4 4" stroke="#fff" stroke-width="1.6" fill="none"/></svg></a>
  </div>

  <div class="card" style="left:620px;top:497px">
    <svg class="card__shot" width="215" height="233" viewBox="0 0 215 233" role="img" aria-label="Apprentice working at a machine">
      <defs><linearGradient id="g4" x1="0" y1="0" x2="1" y2="1"><stop offset="0" stop-color="#c9d0d6"/><stop offset="1" stop-color="#2c3c52"/></linearGradient></defs>
      <polygon points="0,0 215,0 105,233" fill="var(--orange)"/>
      <polygon points="12,0 203,0 105,208" fill="url(#g4)"/>
    </svg>
    <h3 class="card__title">Lorem ipsum dolor</h3>
    <p class="card__text">Lorem ipsum dolor sit amet, consectetur adipiscing elit, sed do eiusmod tempor incididunt ut labore et dolore</p>
    <a class="card__more" href="#"><svg width="12" height="12" viewBox="0 0 12 12"><path d="M2 2l4 4-4 4M6 2l4 4-4 4" stroke="#fff" stroke-width="1.6" fill="none"/></svg></a>
  </div>
</section>

<section class="about">
  <h2 class="section-title">Lernwandel</h2>
  <p class="about__lead">Lernwandel has been organizing the exchange of apprentices between different cultural and language regions within Switzerland as well as with other countries for more than 19 years. Primary participants are all apprentices who are completing their basic vocational education and training. Once registered for the exchange, lernwandel will find a suitable exchange company and an appropriate accommodation, where the apprentice will go through an exchange of at least three weeks. Falkner Circle Switzerland/Liechtenstein mainly supports this program with the objective of promoting the mobility of apprentices.</p>

  <div class="feature-photo" style="left:175px;top:331px;width:425px;height:364px;background:linear-gradient(120deg,#cfd3d6,#eeeae4 50%,#2b2b2f)" role="img" aria-label="Apprentice in a cream sweater working on a laptop"></div>
  <div class="feature-box" style="left:600px;top:352px;width:429px;height:322px">
    <h3>PROFIT</h3>
    <p>By taking part in this exchange programme, you broaden your professional as well as your personal horizon. Not only do you get to know a new environment, the challenge will be for you to adapt to it and demonstrating your high level of flexibility. You meet new people both at home and abroad and make new contacts, which are often maintained even after the exchange is over. Improve your language skills by using them in your daily life and experience a new culture. After successfully finishing your exchange you will receive a lernwandel certificate, verifying your experience and making the entry into the world of work easier for you.</p>
  </div>

  <div class="feature-box feature-box--right" style="left:171px;top:716px;width:429px;height:322px;padding-top:54px">
    <h3>COSTS</h3>
    <p>Your training company continues paying your normal wage during the exchange. Whenever possible you live with a host family, where you have breakfast and dinner. Lernwandel or the local Falkner-Circle will provide financial support for any expenses arising from the accommodation. Only travel costs, lunch and any leisure activities need to be paid by yourself. The mediation and organisation of the exchange is financed by the sponsors of lernwandel.</p>
  </div>
  <div class="feature-photo" style="left:600px;top:694px;width:425px;height:364px;background:linear-gradient(120deg,#9a9a92,#b6d84a 45%,#e9ecef)" role="img" aria-label="Apprentice in a high-visibility jacket filling in a form"></div>
</section>

<section class="stories">
  <svg class="abs" style="left:0;top:0" width="1200" height="357" viewBox="0 0 1200 357">
    <defs>
      <linearGradient id="gb" x1="0" y1="0" x2="0" y2="1"><stop offset="0" stop-color="#1b3566"/><stop offset="1" stop-color="#1a3a70"/></linearGradient>
      <linearGradient id="go" x1="0" y1="0" x2="1" y2="1"><stop offset="0" stop-color="#a63a0a"/><stop offset="1" stop-color="#c9550e"/></linearGradient>
    </defs>
    <polygon points="0,0 634,0 552,357 0,357" fill="url(#gb)" role="img" aria-label="Old town skyline at dusk, tinted blue"/>
    <polygon points="650,0 1200,0 1200,357 567,357" fill="url(#go)" role="img" aria-label="Flower arrangement, tinted orange"/>
  </svg>
  <div class="story__name" style="left:108px">Mira<br>Merchant</div>
  <a class="btn btn--orange" href="#" style="left:112px;top:219px;width:163px;height:39px">View More</a>
  <div class="story__name" style="right:112px;text-align:right">Selin<br>Florist</div>
  <a class="btn btn--blue" href="#" style="left:925px;top:219px;width:164px;height:39px">View More</a>
</section>

<section class="contact">
  <div class="logo">lernwandel</div>
  <div class="info" style="left:110px">
    <div class="info__icon"><svg width="16" height="18" viewBox="0 0 16 18"><path d="M8 1a5.5 5.5 0 0 0-5.5 5.5C2.5 11 8 17 8 17s5.5-6 5.5-10.5A5.5 5.5 0 0 0 8 1z" fill="#fff"/><circle cx="8" cy="6.5" r="2" fill="var(--orange)"/></svg></div>
    <div class="info__label">ADDRESSS :</div>
    <div class="info__value">Lindenweg 12, 8004 Zürich</div>
  </div>
  <div class="info" style="left:447px">
    <div class="info__icon"><svg width="18" height="14" viewBox="0 0 18 14"><rect x="1" y="1" width="16" height="12" rx="1" fill="#fff"/><path d="M1 2l8 6 8-6" stroke="var(--orange)" stroke-width="1.5" fill="none"/></svg></div>
    <div class="info__label">EMAIL ADDRESSS :</div>
    <div class="info__value">info@lernwandel.ch</div>
  </div>
  <div class="info" style="left:784px">
    <div class="info__icon"><svg width="16" height="16" viewBox="0 0 16 16"><path d="M3 1l3 3-1.5 2a9 9 0 0 0 5.5 5.5L12 10l3 3-2 2C7 15 1 9 1 3z" fill="#fff"/></svg></div>
    <div class="info__label">PHONE :</div>
    <div class="info__value">+41 (0) 44 000 12 34</div>
  </div>
</section>

<footer class="site-footer">
  <div class="partner">Falkner Circle <span class="mark"></span></div>
  <p class="legal">© 2023 Company name.All Rights Reserved &nbsp;| Privacy Policy | &nbsp;Terms</p>
  <div class="iban"><h4>IBAN Number</h4><p>CH00 0000 1234 5678 9012 3</p></div>
  <div class="social" style="left:789px" aria-label="WhatsApp"></div>
  <div class="follow">Follow Us :</div>
  <div class="social" style="left:995px" aria-label="Facebook"></div>
  <div class="social" style="left:1046px" aria-label="LinkedIn"></div>
</footer>

</body>
</html>
```